Local fast-growing company in the service sector

We are looking for a modern business card design, which should also appear on our letterheads

Target Market(s)

Private and industrial sectors

Contact Information for Business Card

Vorname Name
Kellberger Str. 18
74398 Lindenau
Tel.: 07146-839214-0
Name@agentur-kvtl.de

Colors
9d9d9d
919191
aaaaaa

Requirements
Must have
• The logo (file) in silver

```html
<!DOCTYPE html>
<html lang="de">
<head>
<meta charset="utf-8">
<title>KVTL Visitenkarte</title>
<link rel="stylesheet" href="https://fonts.googleapis.com/css2?family=Open+Sans:wght@400;600;700&display=swap">
<style>
  :root {
    --backdrop: #3a3330;
    --card: #141414;
    --card-edge: #0c0c0c;
    --silver: #aaaaaa;
    --silver-mid: #9d9d9d;
    --silver-dark: #919191;
    --text-light: #e6e6e6;
    --mark-faint: #262626;
  }
  * { box-sizing: border-box; margin: 0; padding: 0; }
  html, body {
    width: 1200px; height: 864px; overflow: hidden;
    background: var(--backdrop);
    font-family: "Open Sans", Arial, sans-serif;
  }
  .stage {
    position: relative; width: 1200px; height: 864px;
    display: flex; align-items: center; justify-content: center; gap: 40px;
  }
  .card {
    position: relative; width: 520px; height: 336px;
    background: var(--card);
    border: 1px solid var(--card-edge);
    box-shadow: 0 10px 30px rgba(0,0,0,.45);
  }
  .card-back .brand-mark {
    position: absolute; left: 0; right: 0; top: 96px;
    text-align: center; font-weight: 700; font-size: 84px;
    letter-spacing: 4px; color: var(--mark-faint); line-height: 1;
  }
  .card-back .web-line {
    position: absolute; left: 0; right: 0; top: 232px;
    text-align: center; font-size: 14px; letter-spacing: 7px;
    color: var(--silver-dark);
  }
  .card-front .brand-name {
    position: absolute; left: 238px; top: 92px;
    display: flex; align-items: center; gap: 14px;
    font-weight: 700; font-size: 58px; letter-spacing: 2px;
    color: var(--silver); line-height: 1;
  }
  .card-front .brand-square {
    width: 40px; height: 40px; background: var(--silver);
  }
  .person {
    position: absolute; right: 292px; top: 206px;
    text-align: right; font-size: 14px; line-height: 20px;
    color: var(--text-light);
  }
  .person .person-name {
    font-weight: 700; font-size: 13px; letter-spacing: 1px;
    color: var(--silver-dark); text-transform: uppercase;
  }
  .divider {
    position: absolute; left: 244px; top: 208px;
    width: 1px; height: 66px; background: var(--silver-dark);
  }
  .contacts {
    position: absolute; left: 260px; top: 218px;
    list-style: none; font-size: 14px; line-height: 20px;
    color: var(--text-light);
  }
  .contacts li { display: flex; align-items: center; gap: 8px; }
  .contacts svg { width: 11px; height: 11px; fill: var(--silver); flex: none; }
</style>
</head>
<body>
<main class="stage">
  <section class="card card-back" aria-label="Kartenrückseite">
    <div class="brand-mark">KVTL</div>
    <div class="web-line">www.agentur-kvtl.de</div>
  </section>

  <section class="card card-front" aria-label="Kartenvorderseite">
    <div class="brand-name"><span class="brand-square"></span>KVTL</div>

    <div class="person">
      <div class="person-name">Jonas Keller</div>
      <div>Kellberger Str. 18</div>
      <div>74398 Lindenau</div>
    </div>

    <div class="divider"></div>

    <ul class="contacts">
      <li>
        <svg viewBox="0 0 12 12" aria-hidden="true"><path d="M2.5 1 4.5 1 5.3 3.6 4 4.6Q5 7 7.4 8L8.4 6.7 11 7.5 11 9.5Q10.5 11 9 11 1 10.5 1 3 1 1.5 2.5 1Z"/></svg>
        07146-839214-0
      </li>
      <li>
        <svg viewBox="0 0 12 12" aria-hidden="true"><path d="M1 2.5H11V9.5H1Z M1.3 2.8 6 6.6 10.7 2.8" stroke="#141414" stroke-width=".8"/></svg>
        Name@agentur-kvtl.de
      </li>
      <li>
        <svg viewBox="0 0 12 12" aria-hidden="true"><circle cx="6" cy="6" r="5"/><circle cx="6" cy="6" r="2" fill="#141414"/></svg>
        www.agentur-kvtl.de
      </li>
    </ul>
  </section>
</main>
</body>
</html>
```